RWT Fittings Ltd Business Cards

We need a business card with our business logo. We provide window and door installations on high-rises in west coast British Colombia, Canada.

I would like my business information and details on one side of the card, and the other side the company name with logo

Target Market(s)

General Contractors

Industry/Entity Type

Construction

Contact Information for Business Card

one side i want my company name and logo in the dark theme logo that i provided

Requirements
Must have
• Marco Peltieri, 16045518293, RWTFittings@mailbox-demo.com, 1407-5194 Linden Row Burnaby BC, V5H 2K9, Owner & Manager

```html
<!DOCTYPE html>
<html lang="en">
<head>
<meta charset="utf-8">
<title>RWT Fittings Ltd – Business Cards</title>
<link rel="stylesheet" href="https://fonts.googleapis.com/css2?family=Open+Sans:wght@400;600;700&display=swap">
<style>
  :root {
    --page-bg: #3a3a3a;
    --card-white: #ffffff;
    --card-black: #1a1a18;
    --brand-blue: #29a8e0;
    --brand-blue-deep: #1f9ad6;
    --brand-grey: #9a9a9a;
    --text-dark: #2a2a2a;
    --text-light: #ffffff;
  }
  * { box-sizing: border-box; margin: 0; padding: 0; }
  html, body { width: 1200px; height: 780px; overflow: hidden; }
  body {
    background: var(--page-bg);
    font-family: "Open Sans", Arial, sans-serif;
    display: flex;
    align-items: center;
    justify-content: center;
    gap: 40px;
  }
  .card {
    position: relative;
    width: 540px;
    height: 309px;
    overflow: hidden;
    box-shadow: 0 10px 30px rgba(0,0,0,.45);
  }

  /* Front: contact side */
  .card-front { background: var(--card-white); }
  .front-wave { position: absolute; inset: 0; width: 100%; height: 100%; }
  .front-logo {
    position: absolute;
    left: 28px;
    top: 22px;
    display: flex;
    align-items: center;
    gap: 10px;
  }
  .logo-square {
    width: 30px;
    height: 30px;
    background: var(--brand-grey);
  }
  .logo-name {
    font-weight: 700;
    font-size: 22px;
    color: var(--brand-blue);
    letter-spacing: .5px;
  }
  .person {
    position: absolute;
    right: 40px;
    top: 58px;
    text-align: right;
  }
  .person-name {
    font-weight: 700;
    font-size: 21px;
    color: var(--brand-blue);
    line-height: 1.2;
  }
  .person-role {
    font-size: 13px;
    color: var(--text-dark);
    margin-top: 2px;
  }
  .accent-bar {
    position: absolute;
    right: 0;
    top: 64px;
    width: 12px;
    height: 40px;
    background: var(--brand-blue);
  }
  .contact {
    position: absolute;
    right: 22px;
    bottom: 18px;
    text-align: right;
    color: var(--text-light);
    font-size: 13px;
    line-height: 1.45;
  }
  .contact-address { margin-bottom: 10px; padding-right: 21px; }
  .contact-line {
    display: flex;
    align-items: center;
    justify-content: flex-end;
    gap: 8px;
  }
  .contact-icon { width: 13px; height: 13px; flex: none; }

  /* Back: brand side */
  .card-back { background: var(--brand-blue); }
  .back-pattern {
    position: absolute;
    inset: 0;
    background: linear-gradient(135deg, var(--brand-blue) 0%, var(--brand-blue-deep) 100%);
  }
  .back-brand {
    position: absolute;
    inset: 0;
    display: flex;
    align-items: center;
    justify-content: center;
    gap: 16px;
  }
  .back-square {
    width: 48px;
    height: 48px;
    background: var(--text-light);
  }
  .back-name {
    font-weight: 700;
    font-size: 40px;
    color: var(--text-light);
    letter-spacing: 1px;
  }
</style>
</head>
<body>

  <section class="card card-front" aria-label="Business card front">
    <svg class="front-wave" viewBox="0 0 540 309" preserveAspectRatio="none" aria-hidden="true">
      <path d="M0 56 C50 108 140 110 260 114 C380 118 470 124 540 140 L540 309 L0 309 Z" fill="var(--brand-grey)"/>
      <path d="M0 65 C50 117 140 119 260 123 C380 127 470 133 540 150 L540 309 L0 309 Z" fill="var(--card-white)"/>
      <path d="M0 69 C50 121 140 124 260 128 C380 132 470 139 540 156 L540 309 L0 309 Z" fill="var(--brand-blue)"/>
      <path d="M0 76 C50 128 140 132 260 136 C380 140 470 148 540 166 L540 309 L0 309 Z" fill="var(--card-black)"/>
    </svg>

    <div class="front-logo">
      <span class="logo-square"></span>
      <span class="logo-name">RWT Fittings Ltd</span>
    </div>

    <div class="person">
      <p class="person-name">Marco Peltieri</p>
      <p class="person-role">Owner &amp; Manager</p>
    </div>
    <div class="accent-bar"></div>

    <div class="contact">
      <p class="contact-address">1407-5194 Linden Row<br>Burnaby BC, V5H 2K9</p>
      <p class="contact-line">16045518293
        <svg class="contact-icon" viewBox="0 0 24 24" aria-hidden="true"><path d="M6.6 10.8a15 15 0 0 0 6.6 6.6l2.2-2.2c.3-.3.7-.4 1-.2 1.1.4 2.3.6 3.6.6.6 0 1 .4 1 1V20c0 .6-.4 1-1 1C10.6 21 3 13.4 3 4c0-.6.4-1 1-1h3.5c.6 0 1 .4 1 1 0 1.3.2 2.5.6 3.6.1.3 0 .7-.2 1z" fill="var(--brand-blue)"/></svg>
      </p>
      <p class="contact-line">RWTFittings@mailbox-demo.com
        <svg class="contact-icon" viewBox="0 0 24 24" aria-hidden="true"><rect x="2" y="5" width="20" height="14" rx="2" fill="var(--brand-blue)"/><path d="M3 6l9 7 9-7" stroke="var(--card-black)" stroke-width="1.8" fill="none"/></svg>
      </p>
      <p class="contact-line">@RWTFITTINGSLTD
        <svg class="contact-icon" viewBox="0 0 24 24" aria-hidden="true"><circle cx="12" cy="12" r="9" fill="none" stroke="var(--brand-blue)" stroke-width="2.5"/></svg>
      </p>
    </div>
  </section>

  <section class="card card-back" aria-label="Business card back">
    <div class="back-pattern" role="img" aria-label="Faint repeating brand pattern in light and deep blue"></div>
    <div class="back-brand">
      <span class="back-square"></span>
      <span class="back-name">RWT Fittings Ltd</span>
    </div>
  </section>

</body>
</html>
```